Re designing of website of VELTRIS Pens, an International stationary brand

We would like to re design our existing website veltrispens.com. We are leading manufacturers and exporters of stationary products. Our existence is global -selling and marketing in all 5 continents.

We are a 35year old group with focus on high quality, innovative designs and state of art manufacturing setup.

Client satisfaction by committed service and trust are the roots of our organisation.

We would like to see a website which focuses on our brand Veltris and must have an international appeal. Our target buyers would be Agents, distributors and wholesalers in various countries. Content would be similar to our existing website but designing and outlook needs to be totally different.

For the outlook we do like the following websites from our industry which can be used to draw inspiration.
1. www.duniverastationery.com
2. www.quorlapen.com
3. www.haltmivopen.com

The homepage need not be focused on the product but must emphasis on the branding of Veltris, our existence of 35years along with international presence and quality standards maintained by our organisation.
Updates

Reason: Would like to see some more concepts and designs as per artwork attached.

Target Market(s)

Wholesalers, Agents and Distributors in all countries around the world. Target market is global

Number of Pages Required

1 page

Font styles to use
Sans Serif

Requirements
Must have
• Focus on Branding, High Quality Standards, Customer Loyalty
Nice to have
• Like the outlook of the websites
• www.haltmivopen.com
• www.duniverastationery.com
• www.quorlapen.com
Should not have
• Don't like the outlook of our present website www.veltrispens.com
• It doesn't justify our brand or our product

```html
<!DOCTYPE html>
<html lang="en">
<head>
<meta charset="utf-8">
<title>Veltris – World Class Writing Instruments</title>
<link href="https://fonts.googleapis.com/css2?family=Open+Sans:wght@400;600;700;800&display=swap" rel="stylesheet">
<style>
:root{
  --red:#e3202b;
  --red-dark:#b8141d;
  --ink:#2b2b2b;
  --grey:#7a7a7a;
  --light:#f3f3f3;
  --footer:#1b1b1b;
  --footer-deep:#111;
  --white:#fff;
}
*{box-sizing:border-box;margin:0;padding:0}
html,body{width:849px;height:1200px;overflow:hidden;background:var(--white);font-family:"Open Sans",Arial,sans-serif;color:var(--ink)}
.page{position:relative;width:849px;height:1200px}

/* header */
.site-header{height:56px;background:var(--red);display:flex;align-items:center;padding:0 40px 0 30px}
.brand{display:flex;align-items:center;gap:8px;color:var(--white)}
.brand-mark{width:26px;height:26px;background:var(--white)}
.brand-name{font-size:22px;font-weight:700;letter-spacing:1px;line-height:1}
.brand-tag{font-size:7px;font-weight:400;margin-top:2px;letter-spacing:.3px}
.main-nav{margin-left:auto;display:flex;align-items:center;gap:2px}
.main-nav a{color:var(--white);text-decoration:none;font-size:8px;font-weight:600;padding:6px 9px}
.main-nav a.active{background:var(--red-dark)}
.lang{margin-left:12px;background:var(--white);color:var(--red);font-size:8px;font-weight:700;padding:5px 10px}

/* hero */
.hero{position:relative;height:370px;background:#fafafa}
.hero-photo{position:absolute;left:0;top:0;width:440px;height:370px;background:linear-gradient(135deg,#d9dadc 0%,#f4f4f4 45%,#e7e7e7 70%,#cfd0d2 100%)}
.hero-copy{position:absolute;left:470px;top:90px;width:330px}
.hero-title{font-size:24px;font-weight:700;color:#333;letter-spacing:.5px}
.hero-lead{font-size:12px;color:#555;margin-top:8px;line-height:1.35}
.hero-strap{font-size:12px;font-weight:700;color:var(--red);margin-top:14px}
.hero-rule{height:1px;background:#ddd;margin-top:8px;width:290px}
.btn{display:inline-block;margin-top:16px;background:var(--red);color:var(--white);font-size:9px;font-weight:700;padding:9px 20px}
.slider-dots{position:absolute;left:0;right:0;bottom:24px;display:flex;justify-content:center;gap:6px}
.slider-dots span{width:7px;height:7px;border-radius:50%;border:1px solid var(--red)}
.slider-dots span.on{background:var(--red)}

/* intro */
.intro{display:flex;padding:30px 40px 0 40px;gap:40px;height:220px}
.welcome{width:430px}
.section-title{font-size:24px;font-weight:400;color:#333;letter-spacing:.5px}
.section-title em{font-style:normal;color:var(--red)}
.welcome p{font-size:8px;line-height:1.55;color:var(--grey);margin-top:10px}
.events{flex:1}
.events-head{display:flex;align-items:center;justify-content:space-between;border-bottom:1px solid #ddd;padding-bottom:6px}
.events-tools{display:flex;gap:4px;align-items:center}
.events-tools span{font-size:7px;color:var(--grey);border:1px solid #ccc;padding:2px 5px}
.month{background:var(--light);color:#c77;font-size:10px;font-weight:700;padding:5px 8px;margin-top:8px}
.event{display:flex;gap:10px;padding:8px 0;border-bottom:1px solid #eee}
.event-date{width:36px;height:32px;background:#555;color:var(--white);text-align:center;font-size:14px;font-weight:700;line-height:1}
.event-date small{display:block;font-size:6px;font-weight:600;margin-top:2px}
.event-date b{display:block;padding-top:5px}
.event h4{font-size:9px;font-weight:700;color:#333}
.event p{font-size:7px;color:var(--grey);margin-top:3px}

/* countries */
.export{background:var(--red);height:330px;padding:22px 40px 0;color:var(--white);text-align:center}
.export h2{font-size:20px;font-weight:400;letter-spacing:1px}
.export-rule{height:1px;background:rgba(255,255,255,.5);margin:10px 0 12px}
.country-list{display:flex;flex-wrap:wrap;justify-content:center;align-items:baseline;gap:4px 12px;font-weight:700;line-height:1.25}
.s1{font-size:7px}.s2{font-size:10px}.s3{font-size:13px}.s4{font-size:16px}

/* footer */
.site-footer{background:var(--footer);height:224px;color:#bbb;padding:24px 40px 0;position:relative}
.footer-cols{display:flex;gap:40px}
.footer-col{width:140px}
.footer-col.wide{width:220px;margin-left:auto}
.footer-col h5{color:var(--white);font-size:9px;font-weight:700;border-bottom:1px solid #444;padding-bottom:6px;margin-bottom:8px;letter-spacing:.5px}
.footer-col li{list-style:none;font-size:8px;line-height:1.7}
.footer-col p{font-size:8px;line-height:1.5}
.sub-form{display:flex;margin-top:8px}
.sub-form span{flex:1;background:var(--white);color:#999;font-size:7px;padding:7px}
.sub-btn{display:inline-block;background:var(--red);color:var(--white);font-size:7px;font-weight:700;padding:7px 14px;margin-top:8px}
.footer-bar{position:absolute;left:0;right:0;bottom:0;height:62px;background:var(--footer-deep);display:flex;align-items:center;padding:0 40px}
.footer-brand{display:flex;align-items:center;gap:6px;color:var(--white)}
.footer-brand .brand-mark{width:18px;height:18px}
.footer-brand .brand-name{font-size:15px}
.copyright{position:absolute;left:0;right:0;text-align:center;font-size:7px;color:#888}
.social{margin-left:auto;display:flex;gap:5px}
.social span{width:14px;height:14px;border-radius:50%;background:#666}
</style>
</head>
<body>
<div class="page">

<header class="site-header">
  <div class="brand">
    <span class="brand-mark"></span>
    <div>
      <div class="brand-name">VELTRIS</div>
      <div class="brand-tag">World Class Writing Instruments</div>
    </div>
  </div>
  <nav class="main-nav">
    <a class="active">HOME</a>
    <a>ABOUT US</a>
    <a>PRODUCTS</a>
    <a>PROMOTIONAL PRODUCTS</a>
    <a>ENQUIRY FORM</a>
    <a>CONTACT</a>
    <span class="lang">ENGLISH ▾</span>
  </nav>
</header>

<section class="hero">
  <div class="hero-photo" role="img" aria-label="Desk scene with keyboard, metal pen, notepad reading Excellent Writing and a cup of coffee"></div>
  <div class="hero-copy">
    <h1 class="hero-title">VELTRIS METAL PENS</h1>
    <p class="hero-lead">We are leading manufacturers and exporters of stationary products. Our existence is global.</p>
    <p class="hero-strap">Selling and marketing in all 5 continents</p>
    <div class="hero-rule"></div>
    <span class="btn">CONTACT US</span>
  </div>
  <div class="slider-dots"><span class="on"></span><span></span><span></span><span></span></div>
</section>

<section class="intro">
  <div class="welcome">
    <h2 class="section-title">WELCOME TO <em>VELTRIS</em></h2>
    <p>Veltris has crafted fine writing instruments for over thirty five years, pairing careful design with modern manufacturing. Every pen leaves our plant only after strict quality checks, so agents and distributors can offer their buyers lasting value.</p>
    <p>Our products reach partners on all five continents. We build long relationships through committed service, quick delivery and honest trust, the roots of our organisation since the very first day.</p>
    <p>From ball pens to metal gift sets, each range is tested for smooth flow and firm grip.</p>
  </div>
  <div class="events">
    <div class="events-head">
      <h2 class="section-title">EVENTS</h2>
      <div class="events-tools"><span>‹</span><span>TODAY</span><span>›</span></div>
    </div>
    <div class="month">JUNE, 2014</div>
    <div class="event">
      <div class="event-date"><b>20</b><small>JUN</small></div>
      <div><h4>CAMPING TRIP</h4><p>Team outing for our plant staff.</p></div>
    </div>
    <div class="event">
      <div class="event-date"><b>28</b><small>JUN</small></div>
      <div><h4>CINCO DE MAYO</h4><p>Festive day with partners.</p></div>
    </div>
  </div>
</section>

<section class="export">
  <h2>EXPORTING COUNTRIES</h2>
  <div class="export-rule"></div>
  <div class="country-list">
    <span class="s3">ARGENTINA</span><span class="s1">ARMENIA</span><span class="s1">ARUBA</span><span class="s1">AUSTRALIA</span><span class="s3">AUSTRIA</span><span class="s2">AZERBAIJAN</span><span class="s3">BAHAMAS, THE BAHRAIN</span><span class="s1">BANGLADESH</span><span class="s3">BARBADOS</span>
    <span class="s1">BELARUS</span><span class="s1">BELGIUM</span><span class="s1">BELIZE</span><span class="s1">BENIN</span><span class="s1">BHUTAN</span><span class="s1">BOLIVIA</span><span class="s1">BOSNIA AND HERZEGOVINA</span><span class="s3">BOTSWANA</span><span class="s1">BRAZIL</span><span class="s1">BRUNEI</span><span class="s3">BULGARIA</span><span class="s1">BURMA</span>
    <span class="s1">CAMBODIA</span><span class="s2">CANADA</span><span class="s1">CAPE VERDE</span><span class="s1">CENTRAL AFRICAN REPUBLIC</span><span class="s3">CHAD</span><span class="s3">CHILE</span><span class="s1">CHINA</span><span class="s1">COLOMBIA</span><span class="s1">COMOROS</span><span class="s1">CONGO, DEMOCRATIC REPUBLIC</span>
    <span class="s1">OF THE CONGO</span><span class="s1">FRANCE</span><span class="s1">NIGERIA</span><span class="s3">GERMANY</span><span class="s1">GHANA</span><span class="s1">HAITI</span><span class="s1">HONG KONG</span><span class="s1">HUNGARY</span><span class="s3">INDIA</span><span class="s1">INDONESIA</span><span class="s3">IRAN</span><span class="s1">IRAQ</span><span class="s1">IRELAND</span><span class="s1">ITALY</span>
    <span class="s3">JAMAICA</span><span class="s1">JAPAN</span><span class="s3">JORDAN</span>
  </div>
</section>

<footer class="site-footer">
  <div class="footer-cols">
    <div class="footer-col">
      <h5>PRODUCTS</h5>
      <ul><li>Retail Products</li><li>Promotional Products</li></ul>
    </div>
    <div class="footer-col">
      <h5>INFORMATION</h5>
      <ul><li>Order Now!</li><li>Privacy Policy</li><li>Payment Methods</li></ul>
    </div>
    <div class="footer-col">
      <h5>SUPPORT</h5>
      <ul><li>Contact Us</li><li>Our Company</li><li>Follow on Social Media</li></ul>
    </div>
    <div class="footer-col wide">
      <h5>NEWSLETTER SUBSCRIPTION</h5>
      <p>Subscribe to our Newsletter and Get latest Updates</p>
      <div class="sub-form"><span>Email</span></div>
      <span class="sub-btn">SUBSCRIBE</span>
    </div>
  </div>
  <div class="footer-bar">
    <div class="footer-brand"><span class="brand-mark"></span><span class="brand-name">VELTRIS</span></div>
    <div class="copyright">VELTRIS INC. PTY LTD © 2015</div>
    <div class="social"><span></span><span></span><span></span><span></span></div>
  </div>
</footer>

</div>
</body>
</html>
```